New Coffee Shop business card

We are opening our new coffee shop and are needing business cards to take with us on February 6th to Atlanta, Ga to a show.

We will be offering the following menu type items:

coffee
teas
espresso
frappes
smoothies

sandwiches
soups
salads
pastries
ice cream

Our shop is in a rural country-side area and we would like to convey that feel in our shop. In addition to the cafe we will also be selling gifts and furniture and other home decor. Much of this merchandise will be rescued, refurbished or repurposed which is also a core value of what we are all about.

We have a company logo we would like incorporated into the design.

We will also provide files that have the elements of the logo which may also be useful in the design of the card.

Since we are not open yet we need one slightly altered version of the card as well as the final product which states "Opening in the summer 2015"

Target Market(s)

moderate to slightly upscale and folksy.

Industry/Entity Type

Coffee Shop

Contact Information for Business Card

Fern Kettle Coffee
name
address
phone number
email

Card

Font styles to use
Sans Serif

Requirements
Must have
• Must include Logo
• Must include information on menu.
• Must include information on our merchandise sales as described inthe project description.
• Color scheme to complement the logo
Nice to have
• The following descriptions
• "We are also selling gifts, furniture, and other home decoration."
• "We rescue, refurbish, and repurpose old furniture so it can live again."

```html
<!DOCTYPE html>
<html lang="en">
<head>
<meta charset="utf-8">
<title>Fern Kettle Coffee – Business Cards</title>
<link rel="stylesheet" href="https://fonts.googleapis.com/css2?family=Questrial&family=Open+Sans:wght@700&display=swap">
<style>
  :root {
    --bg: #ece8e2;
    --wine: #b8384a;
    --wine-deep: #9c2639;
    --wine-light: #c84b5c;
    --paper: #f4f4f4;
    --ink-grey: #5a5a5c;
    --white: #ffffff;
    --shadow: rgba(60, 30, 20, 0.25);
  }
  * { box-sizing: border-box; margin: 0; padding: 0; }
  html, body { width: 1200px; height: 1000px; overflow: hidden; }
  body {
    background: var(--bg);
    font-family: "Questrial", "Century Gothic", sans-serif;
    position: relative;
  }
  .card {
    position: absolute;
    width: 630px;
    height: 360px;
    border-radius: 4px;
    overflow: hidden;
    box-shadow: 0 12px 30px var(--shadow);
  }

  /* ---------- Front card ---------- */
  .card--front { left: 80px; top: 80px; display: flex; }
  .front__brand {
    width: 215px;
    background: var(--paper);
    display: flex;
    align-items: center;
    justify-content: center;
  }
  .brand-mark { display: flex; align-items: center; gap: 10px; }
  .brand-mark__dot {
    width: 18px; height: 18px; border-radius: 50%;
    background: var(--wine);
  }
  .brand-mark__name {
    color: var(--ink-grey);
    font-size: 30px;
    line-height: 1;
  }
  .front__info {
    flex: 1;
    position: relative;
    background: linear-gradient(160deg, var(--wine-light), var(--wine) 45%, var(--wine-deep));
    color: var(--white);
    padding: 36px 36px 0 34px;
  }
  .front__company { font-size: 27px; letter-spacing: 0.3px; }
  .front__rule { width: 200px; height: 2px; background: var(--white); margin: 16px 0 18px; }
  .front__name { font-family: "Open Sans", sans-serif; font-weight: 700; font-size: 25px; }
  .front__rule--short { margin: 18px 0 16px; }
  .front__details { list-style: none; font-size: 17px; line-height: 1.9; }
  .front__address { margin-bottom: 26px; }
  .front__cup { position: absolute; right: 28px; top: 24px; width: 110px; height: 100px; }

  /* ---------- Back card ---------- */
  .card--back { left: 490px; top: 560px; background: var(--wine); }
  .back__band {
    height: 120px;
    background: var(--paper);
    display: flex;
    align-items: center;
    justify-content: space-between;
    padding: 0 30px;
    color: var(--wine);
    font-family: "Open Sans", sans-serif;
    font-weight: 700;
    font-size: 24px;
  }
  .back__band .brand-mark__name { font-size: 22px; font-family: "Questrial", sans-serif; font-weight: 400; }
  .back__band .brand-mark__dot { width: 13px; height: 13px; }
  .back__flourish {
    position: absolute;
    width: 90px; height: 34px;
    top: 103px;
    background: linear-gradient(90deg, var(--wine-light), var(--white));
    border-radius: 17px;
    opacity: 0.85;
  }
  .back__flourish--left { left: 70px; }
  .back__flourish--right { right: 70px; }
  .back__body {
    position: relative;
    height: 240px;
    background: linear-gradient(170deg, var(--wine-light), var(--wine) 50%, var(--wine-deep));
    color: var(--white);
    padding: 26px 30px;
    display: grid;
    grid-template-columns: 120px 120px 1fr;
    column-gap: 18px;
  }
  .back__menu { list-style: none; font-size: 17px; line-height: 1.45; }
  .back__title { font-size: 34px; line-height: 1; margin-bottom: 16px; }
  .back__note { font-size: 14.5px; line-height: 1.35; }
</style>
</head>
<body>

  <section class="card card--front" aria-label="Business card front">
    <div class="front__brand">
      <div class="brand-mark">
        <span class="brand-mark__dot"></span>
        <span class="brand-mark__name">Fern Kettle</span>
      </div>
    </div>
    <div class="front__info">
      <svg class="front__cup" viewBox="0 0 110 100" aria-hidden="true">
        <path d="M22 10 C8 22 30 30 18 44" fill="none" stroke="#fff" stroke-width="3" stroke-linecap="round"/>
        <path d="M36 6 C22 20 44 28 32 44" fill="none" stroke="#fff" stroke-width="3" stroke-linecap="round"/>
        <path d="M50 40 H92 V60 Q92 78 72 78 H70 Q50 78 50 60 Z" fill="#fff"/>
        <path d="M92 46 Q104 46 104 56 Q104 66 92 66" fill="none" stroke="#fff" stroke-width="4"/>
        <rect x="44" y="82" width="58" height="4" rx="2" fill="#fff"/>
      </svg>
      <p class="front__company">Fern Kettle Coffee</p>
      <div class="front__rule"></div>
      <p class="front__name">John Doe</p>
      <div class="front__rule front__rule--short"></div>
      <ul class="front__details">
        <li class="front__address">Address:</li>
        <li>phone: 123 456 7890</li>
        <li>email: yourname@domaine.com</li>
        <li>Card:</li>
      </ul>
    </div>
  </section>

  <section class="card card--back" aria-label="Business card back, opening announcement">
    <div class="back__band">
      <span>Opening in the</span>
      <div class="brand-mark">
        <span class="brand-mark__dot"></span>
        <span class="brand-mark__name">Fern Kettle</span>
      </div>
      <span>summer 2015</span>
    </div>
    <div class="back__flourish back__flourish--left" role="img" aria-label="Decorative red and white flourish"></div>
    <div class="back__flourish back__flourish--right" role="img" aria-label="Decorative red and white flourish"></div>
    <div class="back__body">
      <ul class="back__menu">
        <li>coffee</li><li>teas</li><li>espresso</li><li>frappes</li><li>smoothies</li>
      </ul>
      <ul class="back__menu">
        <li>sandwiches</li><li>soups</li><li>salads</li><li>pastries</li><li>ice cream</li>
      </ul>
      <div>
        <p class="back__title">coffee shop</p>
        <p class="back__note">We also selling gifts, furniture and other home decoration.<br>We rescue, refurbish or re-purpose your old furniture</p>
      </div>
    </div>
  </section>

</body>
</html>
```